Looking for a dynamic business card for a pizzeria.

A business card with our food, logo, and space for name, title, email, website, phone. The card should convey quality, unique, amazing. On the front, I envision food photo or photos with the owners names and contact information. On the back, more food with locations, website, facebook, twitter, instagram icons. It should look polished, not cartoonish, or plain.
Target Market(s)
upscale, local food buyers, 30-50 years in age.
Industry/Entity Type
Restaurant
Contact Information for Business Card
Business Name: Bru'nettix, LLC
Website: www.brunettix.com
Back:
2 locations: (can list on the back of card)
1. Harbor Point
4087 Corlan Avenue
Larkfield, WA 98463
360-481-5067
2. Cedar Ridge
7315 Wendmere Road
Larkfield, WA 98461
360-293-8840
front:
EDITABLE space for
Business name
Person's Name
title
2nd title
Email address
cell-phone number
Requirements
Must have
- logo
- my food photo or photos (no watermarks showing)
- locations on back
- Person contact information on front
- full bleed

```html
<!DOCTYPE html>
<html lang="en">
<head>
<meta charset="utf-8">
<title>Bru'nettix Business Card</title>
<link rel="stylesheet" href="https://fonts.googleapis.com/css2?family=Arimo:wght@400;700&family=Pinyon+Script&display=swap">
<style>
  :root {
    --backdrop: #4b4b4b;
    --basil: #1f4a25;
    --tomato: #b8160e;
    --brand-red: #c0170f;
    --wood-dark: #4e2a15;
    --wood-mid: #7a4525;
    --wood-light: #94582f;
    --crust: #e9c6a8;
    --pepperoni: #c7542f;
    --cream: #f5ebe0;
    --ink: #1c1c1c;
    --white: #ffffff;
  }
  * { box-sizing: border-box; margin: 0; padding: 0; }
  html, body {
    width: 1105px;
    height: 1200px;
    overflow: hidden;
    background: var(--backdrop);
  }
  .canvas {
    position: relative;
    width: 1105px;
    height: 1200px;
  }

  /* Front of card */
  .card-front {
    position: absolute;
    left: 196px;
    top: 145px;
    width: 720px;
    height: 413px;
    border-radius: 19px;
    overflow: hidden;
    background: var(--wood-mid);
  }
  .front-photo {
    position: absolute;
    left: 0; top: 0;
    width: 720px; height: 217px;
    background:
      radial-gradient(ellipse at 70% 40%, rgba(199,84,47,.85), transparent 55%),
      radial-gradient(ellipse at 20% 70%, rgba(233,198,168,.9), transparent 60%),
      linear-gradient(160deg, var(--crust), var(--pepperoni));
  }
  .brand-name {
    position: absolute;
    left: 0; top: 78px;
    width: 720px;
    text-align: center;
    font-family: "Arimo", sans-serif;
    font-weight: 400;
    font-size: 50px;
    line-height: 60px;
    color: var(--white);
  }
  .red-rule {
    position: absolute;
    left: 0; top: 217px;
    width: 720px; height: 5px;
    background: var(--brand-red);
  }
  .name-band {
    position: absolute;
    left: 0; top: 222px;
    width: 720px; height: 120px;
    background: linear-gradient(90deg, var(--wood-dark), var(--wood-light) 30%, var(--wood-mid) 60%, var(--wood-dark));
    text-align: center;
    color: var(--cream);
    font-family: "Pinyon Script", cursive;
  }
  .person-name {
    display: block;
    font-size: 46px;
    line-height: 1;
    padding-top: 20px;
  }
  .person-title {
    display: block;
    font-size: 32px;
    line-height: 1;
    margin-top: 2px;
  }
  .basil-rule {
    position: absolute;
    left: 0; top: 342px;
    width: 720px; height: 6px;
    background: var(--basil);
  }
  .contact-strip {
    position: absolute;
    left: 0; top: 348px;
    width: 720px; height: 65px;
    background: linear-gradient(90deg, rgba(233,198,168,1), rgba(222,150,110,1) 50%, rgba(233,198,168,1));
    display: flex; align-items: center; justify-content: center;
    font-family: "Arimo", sans-serif;
    font-size: 19px;
    letter-spacing: 1px;
    color: var(--ink);
  }

  /* Back of card */
  .card-back {
    position: absolute;
    left: 196px;
    top: 601px;
    width: 720px;
    height: 414px;
  }
  .wood { fill: url(#woodTone); }
  .photo-pizza { fill: url(#pizzaTone); }
  .photo-sandwich { fill: url(#sandwichTone); }
  .photo-rolls { fill: url(#rollsTone); }
  .location-basil { fill: var(--basil); }
  .location-tomato { fill: var(--tomato); }
  .location-name {
    font-family: "Pinyon Script", cursive;
    font-size: 30px;
    fill: var(--white);
  }
  .location-line {
    font-family: "Arimo", sans-serif;
    font-size: 17.5px;
    fill: var(--white);
  }
</style>
</head>
<body>
<div class="canvas">

  <section class="card-front" aria-label="Business card front">
    <div class="front-photo" role="img" aria-label="Close-up photo of a pepperoni pizza"></div>
    <div class="brand-name">Bru'nettix</div>
    <div class="red-rule"></div>
    <div class="name-band" role="group" aria-label="Wood plank band with name and title">
      <span class="person-name">Marco Bellani</span>
      <span class="person-title">Founder</span>
    </div>
    <div class="basil-rule"></div>
    <div class="contact-strip" role="img" aria-label="Blurred pizza photo behind contact line">
      <span>689 512 7704 | name@brunettix.com | www.brunettix.com</span>
    </div>
  </section>

  <svg class="card-back" viewBox="0 0 720 414" width="720" height="414" aria-label="Business card back">
    <defs>
      <clipPath id="cardShape"><rect width="720" height="414" rx="19"/></clipPath>
      <linearGradient id="woodTone" x1="0" x2="1">
        <stop offset="0" stop-color="#4e2a15"/>
        <stop offset=".35" stop-color="#8a4f2b"/>
        <stop offset=".7" stop-color="#6f3d20"/>
        <stop offset="1" stop-color="#4e2a15"/>
      </linearGradient>
      <linearGradient id="pizzaTone" x1="0" y1="0" x2="1" y2="1">
        <stop offset="0" stop-color="#c45a36"/>
        <stop offset=".5" stop-color="#e7c9ae"/>
        <stop offset="1" stop-color="#b8482a"/>
      </linearGradient>
      <linearGradient id="sandwichTone" x1="0" y1="0" x2="1" y2="1">
        <stop offset="0" stop-color="#d9a95a"/>
        <stop offset=".5" stop-color="#5d8a3a"/>
        <stop offset="1" stop-color="#c99448"/>
      </linearGradient>
      <linearGradient id="rollsTone" x1="0" y1="0" x2="0" y2="1">
        <stop offset="0" stop-color="#f0c58a"/>
        <stop offset=".5" stop-color="#c25a35"/>
        <stop offset="1" stop-color="#ece3d6"/>
      </linearGradient>
    </defs>
    <g clip-path="url(#cardShape)">
      <rect class="wood" width="720" height="414" role="img" aria-label="Wood plank texture"/>
      <polygon class="photo-pizza" points="0,0 238,0 238,106 118,176 0,100" role="img" aria-label="Photo of pepperoni pizza"/>
      <polygon class="photo-sandwich" points="242,0 478,0 478,106 360,174 242,106" role="img" aria-label="Photo of a grilled sandwich"/>
      <polygon class="photo-rolls" points="482,0 720,0 720,100 602,176 482,106" role="img" aria-label="Photo of baked rolls on a tray"/>

      <polygon class="location-basil" points="122,188 240,120 358,188 358,414 122,414"/>
      <polygon class="location-tomato" points="362,188 480,120 598,188 598,414 362,414"/>

      <g text-anchor="middle">
        <text class="location-name" x="240" y="281">Cedar Ridge</text>
        <text class="location-line" x="240" y="337">7315 Wendmere Road</text>
        <text class="location-line" x="240" y="360">Larkfield, WA 98461</text>
        <text class="location-line" x="240" y="383">360-293-8840</text>

        <text class="location-name" x="480" y="281">Harbor Point</text>
        <text class="location-line" x="480" y="337">4087 Corlan Avenue</text>
        <text class="location-line" x="480" y="360">Larkfield, WA 98463</text>
        <text class="location-line" x="480" y="383">360-481-5067</text>
      </g>
    </g>
  </svg>

</div>
</body>
</html>
```